Federal IT Consulting Company - Brisolux Consulting Group

We're seeking a skilled web designer to create a modern, bold, and engaging WordPress website for Brisolux Consulting Group, LLC. Our company specializes in federal IT consulting, and our name is a play on "Brightening Solutions." The website should reflect our expertise in the federal technology marketplace and position us as a trusted partner for clients navigating their IT journey.

contact: info@brisoluxgrp-example.com

Current Status

WordPress is already installed on our hosting account
We have an existing logo (may need modernization)

Design Requirements

Style:

Modern and visually striking design
Bold elements to convey confidence and expertise
Incorporate the concept of "brightening solutions" into the design

Features:

Modern UX sliders for dynamic content presentation
Eye-catching, high-quality images (stock photos to be sourced by the designer)
Responsive design for all devices

Color Scheme:

To be proposed by the designer, should align with our brand and convey trust and technological expertise

Logo:

Evaluate our current logo
Create a transparent background version if needed
Propose modernization if deemed necessary

Accessibility:

Ensure design elements are accessible to users with disabilities
Use high contrast ratios for text and background colors
Provide text alternatives for non-text content

Website Structure
Create the following pages, with the possibility of subpages:

Home
Services
About
Contact

Specific Page Requirements
Home Page

Striking hero section with a clear value proposition
Overview of our services
Client testimonials or trust indicators

Services Page

Detailed list of our IT consulting services
Clear explanation of how we help navigate the federal IT landscape

About Page

Company history and mission
Team highlights (if applicable)
Our approach to federal IT consulting

Contact Page

Contact form
Other contact methods (phone, email)

Technical Requirements

Fully responsive design
SEO best practices implemented
Fast loading times
Integration with necessary plugins (to be discussed)
Training on how to update and maintain the site
Full compliance with Web Content Accessibility Guidelines (WCAG) 2.1 Level AA
Adherence to Section 508 standards for federal website accessibility
Implementation of necessary features for ADA compliance
Updates

Designs look the same

Target Market(s)

US Federal Govt customers looking for IT support.

Industry/Entity Type

IT Consulting

Coding

Coded - Design and coding required

Colors
0054AA
0677BA
7BADD7
CADEEF
E8F1F8
0094D4
00A9DD
6FCCEA
C7EBF8
E9F6FB
00AB8E
00BBA5
67D7C9
C6EFE9
E9F9F6

```html
<!DOCTYPE html>
<html lang="en">
<head>
<meta charset="utf-8">
<title>Brisolux Consulting Group</title>
<link href="https://fonts.googleapis.com/css2?family=Outfit:wght@300;400;500;600&display=swap" rel="stylesheet">
<style>
:root{
  --navy:#2b2a7c;
  --navy-deep:#2e2b6f;
  --accent:#7b73d6;
  --accent-soft:#7873d5;
  --lavender:#f1f1fc;
  --ink:#1a1a2e;
  --muted:#4a4a5a;
  --white:#ffffff;
}
*{box-sizing:border-box;margin:0;padding:0}
html,body{width:1200px;height:3774px;overflow:hidden}
body{position:relative;font-family:'Outfit',sans-serif;color:var(--ink);background:var(--white)}
.abs{position:absolute}
a{color:inherit;text-decoration:none}
.hl{color:var(--accent)}
.label{font-size:12px;letter-spacing:.6px;color:var(--accent);text-transform:uppercase;border-left:2px solid var(--accent);padding-left:8px;line-height:16px}
.h2{font-size:28px;font-weight:500;line-height:36px;color:var(--ink)}
.btn{display:inline-flex;align-items:center;gap:8px;background:var(--navy);color:var(--white);border-radius:24px;font-size:14px;font-weight:500;box-shadow:0 8px 18px rgba(43,42,124,.35);justify-content:center}
.photo{border-radius:24px}
.hero-band{left:0;top:0;width:1200px;height:557px;background:var(--lavender)}
.logo{display:flex;align-items:center;gap:10px;font-size:30px;font-weight:600;color:var(--navy);letter-spacing:1px}
.logo i{width:30px;height:30px;border-radius:50%;border:4px solid currentColor;display:block}
.nav{left:696px;top:26px;display:flex;gap:36px;font-size:14px;font-weight:500}
.nav .on{color:var(--navy)}
.hero-title{left:141px;top:152px;font-size:38px;font-weight:500;line-height:47px}
.hero-sub{right:142px;top:194px;font-size:15px}
.about-text p{font-size:12px;line-height:23px;color:var(--muted);margin-bottom:14px}
.card{width:261px;height:234px;border-radius:12px;overflow:hidden}
.card-cap{position:absolute;left:18px;right:18px;bottom:18px;border:1px solid rgba(255,255,255,.8);border-radius:10px;background:rgba(20,20,50,.45);color:var(--white);padding:14px 14px;font-size:15px;font-weight:500}
.card-cap small{display:block;font-size:12px;font-weight:400;line-height:19px;margin-top:8px;width:160px}
.go{position:absolute;right:14px;bottom:12px;width:24px;height:24px;border-radius:50%;background:var(--white);display:flex;align-items:center;justify-content:center}
.arrowbtn{width:38px;height:38px;border-radius:50%}
.member{width:184px;text-align:center}
.member .pic{width:184px;height:184px;border-radius:50%;overflow:hidden}
.member h4{font-size:15px;font-weight:600;margin-top:18px}
.member span{font-size:11px;color:var(--accent);display:block;margin-top:6px}
.socials{display:flex;gap:10px;justify-content:center;margin-top:14px}
.socials b{width:32px;height:32px;border-radius:50%;background:var(--accent);display:block}
.footer{left:0;top:3443px;width:1200px;height:331px;background:linear-gradient(120deg,#34307c,#26235f 55%,#2c2a6e)}
.fcol h5{font-size:14px;font-weight:500;color:var(--accent);margin-bottom:18px}
.fcol li{list-style:none;font-size:12px;color:var(--white);margin-bottom:12px}
</style>
</head>
<body>

<div class="abs hero-band"></div>
<a class="abs logo" style="left:137px;top:18px" href="#">Brisolux<i></i></a>
<nav class="abs nav"><a class="on" href="#">Home</a><a href="#">About Us</a><a href="#">Services</a></nav>
<a class="abs btn" style="left:950px;top:14px;width:108px;height:42px" href="#">Contact Us</a>

<h1 class="abs hero-title">Navigate Your Federal<br>IT Journey with<br><span class="hl">Confidence</span>.</h1>
<p class="abs hero-sub">Expert Consulting Services to Guide Your IT Strategy.</p>
<a class="abs btn" style="left:870px;top:252px;width:188px;height:42px" href="#">Explore Our Services
  <svg width="12" height="12" viewBox="0 0 12 12"><path d="M2 10L10 2M4 2h6v6" stroke="#fff" stroke-width="1.6" fill="none"/></svg></a>
<div class="abs photo" role="img" aria-label="Capitol building at sunset over a green lawn" style="left:141px;top:345px;width:917px;height:387px;background:
  radial-gradient(ellipse 30% 22% at 50% 52%,rgba(236,236,230,.9),rgba(236,236,230,0)),
  radial-gradient(ellipse 40% 18% at 8% 66%,rgba(244,170,70,.85),rgba(244,170,70,0)),
  radial-gradient(ellipse 22% 26% at 80% 56%,rgba(32,44,30,.9),rgba(32,44,30,0)),
  linear-gradient(180deg,#5f83a6 0%,#9cb4c8 22%,#d9d6cf 42%,#c9b48e 56%,#5c574e 64%,#3f5a2a 72%,#56872f 86%,#4b7a2a 100%)"></div>

<div class="abs label" style="left:141px;top:858px">About Us</div>
<h2 class="abs h2" style="left:141px;top:885px">Why Choose <span class="hl">Brisolux?</span></h2>
<div class="abs about-text" style="left:141px;top:947px;width:425px">
  <p>There are many variations of passages of Lorem Ipsum available, but the majority have suffered alteration in some form, by injected humour, or randomised words which don't look even slightly believable. If you are going to use a passage of Lorem Ipsum, you need to be sure there isn't anything embarrassing hidden in the middle of text.</p>
  <p>It is a long established fact that a reader will be distracted by the readable content of a page when looking at its layout.</p>
</div>
<a class="abs btn" style="left:141px;top:1142px;width:130px;height:42px" href="#">Learn More
  <svg width="12" height="12" viewBox="0 0 12 12"><path d="M2 10L10 2M4 2h6v6" stroke="#fff" stroke-width="1.6" fill="none"/></svg></a>
<div class="abs" style="left:660px;top:825px;width:390px;height:390px;border-radius:50%;background:linear-gradient(135deg,#9aa0ab,#3a3a44 40%,#24242c)"></div>
<div class="abs" role="img" aria-label="Smiling consultant holding a tablet in an office" style="left:678px;top:843px;width:354px;height:354px;border-radius:50%;background:
  radial-gradient(ellipse 30% 36% at 52% 40%,rgba(214,180,150,.85),rgba(214,180,150,0)),
  radial-gradient(ellipse 45% 30% at 50% 88%,rgba(70,90,130,.9),rgba(70,90,130,0)),
  linear-gradient(160deg,#e6eaf0,#b7c3d4 45%,#7f8fa8 100%)"></div>

<div class="abs label" style="left:141px;top:1310px">Popular Services</div>
<h2 class="abs h2" style="left:141px;top:1336px">The Best Solution For<br>Your <span class="hl">Business</span></h2>
<div class="abs arrowbtn" style="left:956px;top:1443px;border:1.5px solid var(--accent)">
  <svg width="35" height="35" viewBox="0 0 35 35"><path d="M25 17.5H10M15 12.5l-5 5 5 5" stroke="#7b73d6" stroke-width="1.8" fill="none"/></svg></div>
<div class="abs arrowbtn" style="left:1020px;top:1443px;background:var(--accent)">
  <svg width="38" height="38" viewBox="0 0 38 38"><path d="M11 19h16M22 14l5 5-5 5" stroke="#fff" stroke-width="1.8" fill="none"/></svg></div>
<div class="abs" role="img" aria-label="Team of colleagues gathered around a desktop computer" style="left:0;top:1450px;width:420px;height:342px;border-radius:0 12px 12px 0;background:
  radial-gradient(ellipse 18% 30% at 70% 48%,rgba(225,225,228,.95),rgba(225,225,228,0)),
  radial-gradient(ellipse 30% 40% at 30% 45%,rgba(40,40,48,.85),rgba(40,40,48,0)),
  radial-gradient(ellipse 60% 22% at 50% 92%,rgba(92,60,38,.95),rgba(92,60,38,0)),
  linear-gradient(135deg,#6f8a5a,#c9c2b4 40%,#9a9088 70%,#5a4030)"></div>
<div class="abs card" style="left:353px;top:1508px" role="img" aria-label="Cybersecurity workstation with glowing monitors">
  <div style="position:absolute;inset:0;background:radial-gradient(ellipse 40% 25% at 30% 20%,rgba(170,80,200,.7),rgba(170,80,200,0)),radial-gradient(ellipse 35% 25% at 75% 30%,rgba(60,160,210,.6),rgba(60,160,210,0)),linear-gradient(170deg,#2c2350,#161830 60%,#2a2248)"></div>
  <div class="card-cap">Cybersecurity<small>There are many variations of passages of Lorem Ipsum available.</small><span class="go"><svg width="10" height="10" viewBox="0 0 12 12"><path d="M2 10L10 2M4 2h6v6" stroke="#2b2a7c" stroke-width="1.8" fill="none"/></svg></span></div>
</div>
<div class="abs card" style="left:632px;top:1508px" role="img" aria-label="Hand touching a glowing cloud interface">
  <div style="position:absolute;inset:0;background:radial-gradient(ellipse 28% 24% at 50% 45%,rgba(255,170,90,.9),rgba(255,170,90,0)),radial-gradient(ellipse 50% 40% at 50% 40%,rgba(130,210,230,.55),rgba(130,210,230,0)),linear-gradient(160deg,#2f6a80,#183650 60%,#2c5c70)"></div>
  <div class="card-cap">Cloud Services<span class="go"><svg width="10" height="10" viewBox="0 0 12 12"><path d="M2 10L10 2M4 2h6v6" stroke="#2b2a7c" stroke-width="1.8" fill="none"/></svg></span></div>
</div>
<div class="abs card" style="left:912px;top:1508px" role="img" aria-label="Meeting room with people working on laptops">
  <div style="position:absolute;inset:0;background:radial-gradient(ellipse 40% 30% at 60% 20%,rgba(150,190,120,.8),rgba(150,190,120,0)),radial-gradient(ellipse 50% 30% at 40% 60%,rgba(60,50,50,.7),rgba(60,50,50,0)),linear-gradient(160deg,#c49a58,#7a6248 50%,#d2a870)"></div>
  <div class="card-cap">IT Strategy Consulting<span class="go"><svg width="10" height="10" viewBox="0 0 12 12"><path d="M2 10L10 2M4 2h6v6" stroke="#2b2a7c" stroke-width="1.8" fill="none"/></svg></span></div>
</div>

<div class="abs" style="left:0;top:1877px;width:1200px;height:519px;background:var(--navy-deep)"></div>
<div class="abs label" style="left:141px;top:1994px;color:var(--white);border-color:var(--white)">Our Testimonials</div>
<h2 class="abs h2" style="left:141px;top:2021px;color:var(--white)">Trusted Client And <span class="hl">Partners</span></h2>
<div class="abs" style="left:868px;top:2172px;width:190px;height:166px;border-radius:12px;background:#4e4a94"></div>
<svg class="abs" style="left:976px;top:2030px" width="40" height="80" viewBox="0 0 40 80" aria-hidden="true">
  <g fill="#6fb8ff"><circle cx="4" cy="4" r="2"/><circle cx="20" cy="4" r="2"/><circle cx="36" cy="4" r="2"/><circle cx="4" cy="22" r="2"/><circle cx="20" cy="22" r="2"/><circle cx="36" cy="22" r="2"/><circle cx="4" cy="40" r="2"/><circle cx="20" cy="40" r="2"/><circle cx="36" cy="40" r="2"/><circle cx="4" cy="58" r="2"/><circle cx="20" cy="58" r="2"/><circle cx="36" cy="58" r="2"/></g></svg>
<div class="abs" role="img" aria-label="Presenter showing a chart to a team in a meeting" style="left:600px;top:1993px;width:371px;height:255px;border-radius:12px;background:
  radial-gradient(ellipse 16% 18% at 64% 30%,rgba(30,40,60,.85),rgba(30,40,60,0)),
  radial-gradient(ellipse 40% 25% at 45% 78%,rgba(230,230,235,.9),rgba(230,230,235,0)),
  radial-gradient(ellipse 20% 35% at 85% 55%,rgba(210,160,170,.8),rgba(210,160,170,0)),
  linear-gradient(135deg,#b9bec8,#8a93a4 40%,#a7b0c0 70%,#6e7a94)"></div>
<div class="abs arrowbtn" style="left:944px;top:2282px;width:34px;height:34px;border:1.5px solid var(--white)">
  <svg width="31" height="31" viewBox="0 0 31 31"><path d="M22 15.5H9M13 11.5l-4 4 4 4" stroke="#fff" stroke-width="1.6" fill="none"/></svg></div>
<div class="abs arrowbtn" style="left:1001px;top:2282px;width:34px;height:34px;background:var(--white)">
  <svg width="34" height="34" viewBox="0 0 34 34"><path d="M10 17h14M20 13l4 4-4 4" stroke="#2b2a7c" stroke-width="1.6" fill="none"/></svg></div>
<div class="abs" style="left:258px;top:2109px;width:371px;height:226px;background:var(--white);border-radius:12px;padding:22px 21px">
  <div role="img" aria-label="Client portrait" style="width:56px;height:56px;border-radius:50%;background:radial-gradient(circle at 50% 40%,#e0b9a0,#8a3a38 70%)"></div>
  <svg style="position:absolute;right:20px;top:28px" width="96" height="16" viewBox="0 0 96 16" aria-label="Five stars">
    <g fill="#f5a623"><path id="s" d="M8 1l2 5h5l-4 3 2 5-5-3-5 3 2-5-4-3h5z"/><use href="#s" x="20"/><use href="#s" x="40"/><use href="#s" x="60"/><use href="#s" x="80"/></g></svg>
  <h4 style="font-size:13px;font-weight:600;margin-top:12px">Miles R. Hartwell</h4>
  <p style="font-size:10px;color:#777;margin-top:4px">CEO &amp; Founder</p>
  <p style="font-size:10px;line-height:20px;color:var(--muted);margin-top:14px">It is a long established fact that a reader will be distracted by the readable content of a page when looking at its layout. The point of using Lorem Ipsum is that it has a more-or-less normal distribution.</p>
</div>

<div class="abs label" style="left:561px;top:2482px">Our Team</div>
<h2 class="abs h2" style="left:0;width:1200px;text-align:center;top:2508px">Meet The Our <span class="hl">Experts</span></h2>
<div class="abs member" style="left:174px;top:2595px"><div class="pic" role="img" aria-label="Portrait of Clara Venn" style="background:radial-gradient(ellipse 22% 22% at 50% 34%,#e5c3ad,rgba(229,195,173,0)),radial-gradient(ellipse 55% 35% at 50% 95%,#2c3564,rgba(44,53,100,0)),radial-gradient(circle at 50% 40%,#f4f2ff,#d9d5f2)"></div><h4>Clara Venn</h4><span>Web Designer</span><div class="socials"><b aria-label="Profile link"></b><b aria-label="Profile link"></b></div></div>
<div class="abs member" style="left:396px;top:2595px"><div class="pic" role="img" aria-label="Portrait of Owen Tarrell" style="background:radial-gradient(ellipse 22% 22% at 50% 34%,#c89a7a,rgba(200,154,122,0)),radial-gradient(ellipse 55% 35% at 50% 95%,#1e1e26,rgba(30,30,38,0)),radial-gradient(circle at 50% 40%,#f4f2ff,#d9d5f2)"></div><h4>Owen Tarrell</h4><span>Web Designer</span><div class="socials"><b aria-label="Profile link"></b><b aria-label="Profile link"></b></div></div>
<div class="abs member" style="left:618px;top:2595px"><div class="pic" role="img" aria-label="Portrait of Nadia Brook" style="background:radial-gradient(ellipse 22% 22% at 50% 34%,#d8ad92,rgba(216,173,146,0)),radial-gradient(ellipse 55% 35% at 50% 95%,#8fb4e0,rgba(143,180,224,0)),radial-gradient(circle at 50% 40%,#f4f2ff,#d9d5f2)"></div><h4>Nadia Brook</h4><span>Web Designer</span><div class="socials"><b aria-label="Profile link"></b><b aria-label="Profile link"></b></div></div>
<div class="abs member" style="left:841px;top:2595px"><div class="pic" role="img" aria-label="Portrait of Ethan Marlow" style="background:radial-gradient(ellipse 22% 22% at 50% 34%,#d1a486,rgba(209,164,134,0)),radial-gradient(ellipse 55% 35% at 50% 95%,#1f2536,rgba(31,37,54,0)),radial-gradient(circle at 50% 40%,#f4f2ff,#d9d5f2)"></div><h4>Ethan Marlow</h4><span>Web Designer</span><div class="socials"><b aria-label="Profile link"></b><b aria-label="Profile link"></b></div></div>

<div class="abs" style="left:141px;top:3028px;width:917px;height:329px;border-radius:50px;background:var(--accent-soft)"></div>
<h2 class="abs" style="left:198px;top:3074px;font-size:26px;font-weight:500;line-height:44px;color:var(--white)">We Are Consulting Group<br>We Make Future!</h2>
<p class="abs" style="left:198px;top:3178px;width:420px;font-size:13px;line-height:23px;color:var(--white)">There are many variations of passages of Lorem Ipsum available, but the majority have suffered alteration in some form.</p>
<a class="abs btn" style="left:198px;top:3263px;width:145px;height:42px;background:var(--white);color:var(--accent);border-radius:4px;box-shadow:none" href="#">Get Started Now</a>
<svg class="abs" style="left:360px;top:3240px" width="130" height="90" viewBox="0 0 130 90" aria-hidden="true">
  <path d="M5 85c10-30 40-10 30-30S80 30 110 12" stroke="#fff" stroke-width="1.2" stroke-dasharray="4 4" fill="none"/>
  <path d="M100 8l22-6-10 20-4-8z" stroke="#fff" stroke-width="1.2" fill="none"/></svg>
<div class="abs" role="img" aria-label="Smiling consultant in glasses and beige suit holding a laptop" style="left:690px;top:2965px;width:240px;height:392px;border-radius:90px 90px 0 0;background:
  radial-gradient(ellipse 22% 12% at 50% 14%,rgba(205,150,120,.95),rgba(205,150,120,0)),
  radial-gradient(ellipse 8% 20% at 52% 42%,rgba(200,40,50,.9),rgba(200,40,50,0)),
  radial-gradient(ellipse 45% 16% at 55% 80%,rgba(120,120,125,.95),rgba(120,120,125,0)),
  linear-gradient(180deg,rgba(120,115,213,0) 0%,#d9c2a6 25%,#cfb598 60%,#b79e83 100%)"></div>

<div class="abs footer"></div>
<a class="abs logo" style="left:141px;top:3508px;font-size:40px;color:var(--white)" href="#">Brisolux<i style="width:38px;height:38px"></i></a>
<div class="abs fcol" style="left:511px;top:3515px"><h5>Quick Links</h5><ul><li>Home</li><li>About Us</li><li>Services</li></ul></div>
<div class="abs fcol" style="left:673px;top:3515px"><h5>Resources</h5><ul><li>Privacy Policy</li><li>Terms Of Service</li></ul></div>
<div class="abs fcol" style="left:852px;top:3515px;width:220px"><h5>Contact Info</h5>
  <ul>
    <li style="display:flex;gap:10px"><svg width="14" height="16" viewBox="0 0 14 16"><path d="M7 15s5-5 5-9A5 5 0 0 0 2 6c0 4 5 9 5 9z" fill="#7b73d6"/><circle cx="7" cy="6" r="2" fill="#2e2b72"/></svg><span>123 Lorem Ipsum Dummy, #567<br>Dummy Road 1234</span></li>
    <li style="display:flex;gap:10px;margin-top:16px"><svg width="14" height="12" viewBox="0 0 14 12"><rect width="14" height="11" rx="1" fill="#7b73d6"/><path d="M1 1l6 5 6-5" stroke="#2e2b72" fill="none"/></svg><span>info@brisoluxgrp-example.com</span></li>
    <li style="display:flex;gap:10px;margin-top:16px"><svg width="14" height="14" viewBox="0 0 14 14"><path d="M3 1l3 3-2 2c1 2 2 3 4 4l2-2 3 3-2 2C6 13 1 8 1 3z" fill="#7b73d6"/></svg><span>555-014-2290</span></li>
  </ul></div>
<div class="abs" style="left:141px;top:3710px;width:917px;height:1px;background:rgba(255,255,255,.25)"></div>
<p class="abs" style="left:141px;top:3736px;font-size:12px;color:var(--white)">© 2024 Brisolux Consulting Group. All rights reserved.</p>
<div class="abs" style="left:908px;top:3730px;display:flex;gap:12px" aria-label="Social links">
  <b style="width:28px;height:28px;border-radius:50%;background:var(--accent);display:block"></b>
  <b style="width:28px;height:28px;border-radius:50%;background:var(--accent);display:block"></b>
  <b style="width:28px;height:28px;border-radius:50%;background:var(--accent);display:block"></b>
  <b style="width:28px;height:28px;border-radius:50%;background:var(--accent);display:block"></b>
</div>

</body>
</html>
```